CBD AgriBusiness Verdant Trophy Business Card

We are HiTec producer of medical cannabis CBD Switzerland of high quality. Our website is alpinleaf.net, we will also revisit it graphically, the winner of this contest will be the graphic designer chosen for the new design of the website. We stand out by the skill of the team, many of our engineers we win cup cannabis. I join the current map to take as an example but to revisit completely: deletion of surname and first name, modification of funds (front / back), reorganization of text info, highlighting the address of the website. three characteristics define the business card: Professional, Class, refined. The business card must be optimized for soft-touch and selective varnish printing.

Target Market(s)

Customers and Suppliers

Industry/Entity Type

Agribusiness

Contact Information for Business Card

Logo, Tél / Whatsapp, mail, url du site : alpinleaf.net

Font styles to use
Sans Serif

Requirements
Must have
• Logo of alpinleaf.net
Nice to have
• a design that stands out well on the selective varnish
Should not have
• Last name and first name

```html
<!DOCTYPE html>
<html lang="en">
<head>
<meta charset="utf-8">
<title>alpinleaf business card</title>
<link rel="stylesheet" href="https://fonts.googleapis.com/css2?family=Work+Sans:wght@400;500;700&display=swap">
<style>
  :root {
    --backdrop: #1c1c1c;
    --card: #262626;
    --card-edge: #2e2e2e;
    --varnish: #4a4a4a;
    --ink: #f4f4f4;
    --accent: #8fd16a;
  }
  * { margin: 0; padding: 0; box-sizing: border-box; }
  html, body {
    width: 1200px; height: 900px; overflow: hidden;
    background: var(--backdrop);
    font-family: "Work Sans", sans-serif;
  }
  .canvas {
    width: 1200px; height: 900px;
    display: flex; flex-direction: column; align-items: center; justify-content: center; gap: 40px;
  }
  .card {
    width: 700px; height: 390px;
    background: var(--card);
    border: 1px solid var(--card-edge);
    position: relative;
  }
  .card-front { display: flex; align-items: center; justify-content: center; }
  .brand {
    display: flex; align-items: center; gap: 14px;
    font-weight: 700; letter-spacing: -0.5px;
  }
  .brand-square { width: 30px; height: 30px; }
  .card-front .brand { font-size: 64px; color: var(--varnish); }
  .card-front .brand-square { background: var(--varnish); }
  .card-back .brand {
    position: absolute; left: 70px; top: 160px;
    font-size: 54px; color: var(--ink);
  }
  .card-back .brand-square { width: 26px; height: 26px; background: var(--accent); }
  .divider {
    position: absolute; left: 372px; top: 70px;
    width: 2px; height: 250px; background: var(--accent);
  }
  .details {
    position: absolute; left: 400px; top: 70px; height: 250px;
    display: flex; flex-direction: column; justify-content: center;
    color: var(--ink);
  }
  .address { font-size: 18px; line-height: 1.45; letter-spacing: 0.5px; }
  .contacts { list-style: none; margin-top: 16px; font-size: 18px; letter-spacing: 0.5px; }
  .contacts li { display: flex; align-items: center; gap: 10px; line-height: 1.6; }
  .contacts svg { width: 14px; height: 14px; flex: none; }
  .web-name { color: var(--accent); }
</style>
</head>
<body>
<main class="canvas">
  <section class="card card-front">
    <div class="brand"><span class="brand-square"></span><span>alpinleaf</span></div>
  </section>

  <section class="card card-back">
    <div class="brand"><span class="brand-square"></span><span>alpinleaf</span></div>
    <div class="divider"></div>
    <div class="details">
      <p class="address">48b Harbour Lane,<br>Westbrook, NZ, 4021</p>
      <ul class="contacts">
        <li>
          <svg viewBox="0 0 16 16" fill="none" stroke="#8fd16a" stroke-width="1.6"><path d="M3 2h3l1.5 3.5-2 1.2a8 8 0 0 0 3.8 3.8l1.2-2L14 10v3a1 1 0 0 1-1 1A11 11 0 0 1 2 3a1 1 0 0 1 1-1z"/></svg>
          <span>+41 (0) 70 555 01 23</span>
        </li>
        <li>
          <svg viewBox="0 0 16 16" fill="none" stroke="#8fd16a" stroke-width="1.6"><rect x="4" y="1.5" width="8" height="13" rx="1.2"/><line x1="7" y1="12" x2="9" y2="12"/></svg>
          <span>+44 7700 90 01 48</span>
        </li>
        <li>
          <svg viewBox="0 0 16 16" fill="none" stroke="#8fd16a" stroke-width="1.6"><rect x="1.5" y="3.5" width="13" height="9" rx="1"/><path d="M1.5 4l6.5 5 6.5-5"/></svg>
          <span>office@alpinleaf.net</span>
        </li>
        <li>
          <svg viewBox="0 0 16 16" fill="none" stroke="#8fd16a" stroke-width="1.4"><circle cx="8" cy="8" r="6.5"/><ellipse cx="8" cy="8" rx="3" ry="6.5"/><line x1="1.5" y1="8" x2="14.5" y2="8"/></svg>
          <span>www.<span class="web-name">alpinleaf</span>.net</span>
        </li>
      </ul>
    </div>
  </section>
</main>
</body>
</html>
```